KorvaNest - Home Income and Business Resources Platform

I am looking for a website template for a multi-purposed website. This website will feature:

1.) Website Directory with Ratings & comments on listings
2.) Company Blog
3.) Homepage with Content (see files for homepage mock)

I would like the Design to have a default width 1170px (wider then normal)

Of course I am looking for Pages for Listings to be designed.

Great looking BLOG Layout: http://journal.plimworks.example/html/blog.html

I would like 4 Versions of a Website Directory Listing "Box"
1.) Basic Listing Box
2.) Sponsored Listing Box
3.) Recommended Listing Box
4.) Stay Away From Listing Box

Information on the Listing Page (Like on a Category Page)
Site Name, Site URL, Website Image, # of Views, Rating and # of Comments

Information on the Listing Details Page:
Same as ABOVE + About website Description, Vornic Score, Category Information

Decent looking examples is here: https://samples.trevolin.example/directory/computers/ and http://www.zqrankhub.example/.

I will include some sketches and screenshots of things I like/looking for. As designers,you have creative freedom and are encouraged to show this. This is Phase one of this project and winning designer is guaranteed to have future work for this project.

Target Market(s)

Directory, business, websites

Industry/Entity Type

Business

Coding

Coded - Design and coding required

Number of Pages Required

5+ page

Font styles to use
Sans Serif

Colors

Designer to choose colors to be used in the design.

Requirements
Must have
• Professional yet clean look. The use of Icons & images
• Unique Look
Should not have
• Any exact copies of any examples I provided

```html
<!DOCTYPE html>
<html lang="en">
<head>
<meta charset="utf-8">
<title>Contact – KorvaNest</title>
<link rel="stylesheet" href="https://fonts.googleapis.com/css2?family=Lato:wght@700;900&family=Open+Sans:wght@400;600&display=swap">
<style>
:root{
  --orange:#f08a2c;
  --ink:#2b2b2b;
  --muted:#5f5f5f;
  --rule:#c9c9c9;
  --footer:#212121;
  --white:#fff;
}
*{margin:0;padding:0;box-sizing:border-box}
html,body{width:1200px;height:1149px;overflow:hidden;background:var(--white)}
body{position:relative;font-family:'Open Sans',sans-serif;color:var(--muted)}
.abs{position:absolute}
.topbar{left:0;top:0;width:1200px;height:3px;background:var(--orange)}
.header{left:0;top:3px;width:1200px;height:78px;border-bottom:1px solid #e2e2e2;box-shadow:0 1px 3px rgba(0,0,0,.06)}
.brand{left:97px;top:31px;font:700 23px/1 'Lato',sans-serif;color:var(--ink);letter-spacing:.2px}
.nav{font:700 15px/1 'Lato',sans-serif;color:var(--ink);top:38px}
.nav.active{color:var(--orange)}
.search{left:987px;top:37px}
.login{left:1021px;top:27px;width:80px;height:35px;border:1px solid #bdbdbd;color:var(--orange);font:700 15px/33px 'Lato',sans-serif;display:flex;align-items:center;justify-content:center;gap:6px}
.hero{left:0;top:81px;width:1200px;height:292px;background:linear-gradient(90deg,#eeeeec 0%,#ebe9e6 45%,#d8cfc8 62%,#b9a79c 75%,#c98aa0 90%,#d7a0b2 100%)}
.hero-title{left:100px;top:196px;font:900 51px/1 'Lato',sans-serif;color:var(--ink);letter-spacing:.5px}
.crumbs{left:98px;top:395px;font:700 16px/1 'Lato',sans-serif;color:#555}
.crumbs .sep{margin:0 6px;font-size:13px}
.crumbs .here{color:var(--orange)}
.rule{left:99px;top:431px;width:1002px;height:1px;background:var(--rule)}
h2{font:900 21px/1 'Lato',sans-serif;color:var(--ink)}
.form-title{left:98px;top:506px}
.field-label{left:98px;font-size:13px;color:#555}
.field-line{left:99px;width:540px;height:1px;background:var(--rule)}
.textarea{left:99px;top:827px;width:540px;height:98px;border:1px solid var(--rule)}
.submit{left:99px;top:960px;width:105px;height:40px;background:var(--orange);color:var(--white);font:700 15px/40px 'Lato',sans-serif;text-align:center;letter-spacing:.4px}
.card{left:678px;top:507px;width:423px;height:482px;border:1px solid #c4c4c4}
.card-title{left:711px;top:541px}
.intro{left:711px;top:581px;width:370px;font-size:14px;line-height:26px;color:#666}
.icon{width:42px;height:42px}
.info{left:774px;font-size:14px;line-height:23px;color:#666}
.connect{left:711px;top:865px}
.social{width:43px;height:43px;border-radius:50%}
.social.one{left:711px;top:912px;background:#345189}
.social.two{left:765px;top:912px;background:#1fa9ec}
.footer{left:0;top:1081px;width:1200px;height:68px;background:var(--footer);color:#f2f2f2;font-size:12px;text-align:center;line-height:66px}
</style>
</head>
<body>
<div class="abs topbar"></div>
<header class="abs header"></header>
<div class="abs brand">KORVANEST</div>
<nav>
  <span class="abs nav" style="left:330px">HOME</span>
  <span class="abs nav" style="left:406px">ABOUT US</span>
  <span class="abs nav" style="left:511px">RESOURCES</span>
  <span class="abs nav" style="left:626px">BUSINESS DIRECTORY</span>
  <span class="abs nav" style="left:812px">NEWS</span>
  <span class="abs nav active" style="left:886px">CONTACT</span>
</nav>
<svg class="abs search" width="15" height="15" viewBox="0 0 15 15" aria-hidden="true"><circle cx="6" cy="6" r="4.6" fill="none" stroke="#2b2b2b" stroke-width="2"/><line x1="9.4" y1="9.4" x2="13.5" y2="13.5" stroke="#2b2b2b" stroke-width="2.4" stroke-linecap="round"/></svg>
<div class="abs login"><svg width="10" height="12" viewBox="0 0 10 12" aria-hidden="true"><path d="M2.5 5V3.5a2.5 2.5 0 0 1 5 0V5" fill="none" stroke="#f08a2c" stroke-width="1.6"/><rect x="0.5" y="5" width="9" height="7" rx="1" fill="#f08a2c"/></svg>LOGIN</div>

<div class="abs hero" role="img" aria-label="Photo of a smiling couple looking at a laptop on a bright background"></div>
<h1 class="abs hero-title">CONTACT</h1>

<div class="abs crumbs">HOME<span class="sep">&gt;&gt;</span><span class="here">CONTACT</span></div>
<div class="abs rule"></div>

<h2 class="abs form-title">WE’RE HERE TO HELP!</h2>
<span class="abs field-label" style="top:555px">Name :</span><div class="abs field-line" style="top:584px"></div>
<span class="abs field-label" style="top:615px">Email :</span><div class="abs field-line" style="top:644px"></div>
<span class="abs field-label" style="top:675px">Phone Number :</span><div class="abs field-line" style="top:704px"></div>
<span class="abs field-label" style="top:735px">Address :</span><div class="abs field-line" style="top:764px"></div>
<span class="abs field-label" style="top:797px">Message :</span>
<div class="abs textarea"></div>
<div class="abs submit">SUBMIT</div>

<div class="abs card"></div>
<h2 class="abs card-title">GETTING IN TOUCH</h2>
<p class="abs intro">Nam libero tempore, cum soluta nobis est eligendi optio cumque nihil impedit quo minus id.</p>

<svg class="abs icon" style="left:712px;top:660px" viewBox="0 0 42 42" aria-hidden="true"><circle cx="21" cy="21" r="20" fill="#fff" stroke="#cfcfcf"/><path d="M21 13a5 5 0 0 0-5 5c0 4 5 10 5 10s5-6 5-10a5 5 0 0 0-5-5z" fill="#f08a2c"/><circle cx="21" cy="18" r="1.8" fill="#fff"/></svg>
<p class="abs info" style="top:659px">At vero eos et accusamus et iusto<br>1875, Newyork</p>

<svg class="abs icon" style="left:712px;top:720px" viewBox="0 0 42 42" aria-hidden="true"><circle cx="21" cy="21" r="20" fill="#fff" stroke="#cfcfcf"/><path d="M15.5 14.5l2.6-.6 1.6 3.6-1.7 1.3a9 9 0 0 0 4.2 4.2l1.3-1.7 3.6 1.6-.6 2.6c-7 .5-11.5-4-11-11z" fill="#f08a2c"/></svg>
<p class="abs info" style="top:730px">1 555 010 2040</p>

<svg class="abs icon" style="left:712px;top:784px" viewBox="0 0 42 42" aria-hidden="true"><circle cx="21" cy="21" r="20" fill="#fff" stroke="#cfcfcf"/><rect x="13" y="15" width="16" height="12" rx="1" fill="#f08a2c"/><path d="M13.5 16l7.5 6 7.5-6" fill="none" stroke="#fff" stroke-width="1.4"/></svg>
<p class="abs info" style="top:794px">info@korvanest.example</p>

<h2 class="abs connect">CONNECT WITH US!</h2>
<div class="abs social one" aria-label="Social profile"></div>
<div class="abs social two" aria-label="Social profile"></div>

<footer class="abs footer">Copyright © 2017. KorvaNest. All Rights Reserved.</footer>
</body>
</html>
```